Business card design for holistic health care clinic

We need a double-sided business card design for our holistic health care clinic that integrates our logo design and also its color scheme. My business is called Valmira. It is an integrative medicine clinic. You have already done the logo for me. Please ensure an elegant and upscale design that is not cluttered, but still has all the necessary information (please see below for details).

Target Market(s)

Wellness, fitness, rehabilitation for educated, well-traveled open-minded clients who are focused on natural, organic, balanced and preventive healthcare and lifestyle.

Industry/Entity Type

Medical

Contact Information for Business Card

Modern, clean.

Number of Pages Required

1 page

Font styles to use
Serif
Sans Serif

Colors

Designer to choose colors to be used in the design.

Requirements
Must have
• Logo on one side, all other information on the other side.
• Other information should include:
• Tobias Wrenfeld - DOE, CPT, LMT
• 4100 East Marrow Drive
• Austin, TX 78119
• 512 555 0148
• 818 555 0192
• info@ValmiraHealth.example
• t.wrenfeld@ValmiraHealth.example
Nice to have
• Darker background on front - but not totally black - shaded/dark gray.

```html
<!DOCTYPE html>
<html lang="en">
<head>
<meta charset="utf-8">
<title>Valmira Business Card</title>
<link rel="stylesheet" href="https://fonts.googleapis.com/css2?family=Source+Sans+3:wght@400;500;600;700;800&display=swap">
<style>
  :root {
    --backdrop: #000000;
    --brand-blue: #0a91cd;
    --card-white: #ffffff;
    --ink: #2b2b2b;
  }
  html, body {
    margin: 0;
    padding: 0;
    width: 1200px;
    height: 900px;
    overflow: hidden;
    background: var(--backdrop);
    font-family: "Source Sans 3", "Myriad Pro", sans-serif;
  }
  .canvas { position: relative; width: 1200px; height: 900px; }
  .card {
    position: absolute;
    top: 300px;
    width: 442px;
    height: 273px;
    overflow: hidden;
  }
  .card--back { left: 152px; background: var(--card-white); }
  .card--front { left: 622px; background: var(--brand-blue); }

  .wordmark {
    position: absolute;
    margin: 0;
    font-weight: 800;
    line-height: 1;
    text-align: center;
    letter-spacing: 0.5px;
  }
  .tagline {
    position: absolute;
    margin: 0;
    font-weight: 700;
    text-align: center;
    line-height: 1;
  }
  .card--back .wordmark { left: 20px; width: 200px; top: 104px; font-size: 42px; color: var(--brand-blue); }
  .card--back .tagline { left: 20px; width: 200px; top: 143px; font-size: 12.5px; color: var(--brand-blue); }

  .card--front .wordmark { left: 0; width: 442px; top: 118px; font-size: 62px; color: var(--card-white); }
  .card--front .tagline { left: 0; width: 442px; top: 177px; font-size: 18px; color: var(--card-white); }

  .holder { position: absolute; left: 236px; top: 38px; margin: 0; }
  .holder__name { margin: 0; font-size: 18px; font-weight: 700; color: var(--brand-blue); letter-spacing: 0.3px; line-height: 1; }
  .holder__credentials { margin: 8px 0 0 1px; font-size: 12px; color: var(--ink); line-height: 1; }

  .contact-list {
    position: absolute;
    left: 237px;
    top: 94px;
    margin: 0;
    padding: 0;
    list-style: none;
    font-size: 12px;
    color: var(--ink);
  }
  .contact-list li { display: flex; align-items: center; height: 16px; white-space: nowrap; }
  .contact-list svg { width: 10px; height: 10px; margin-right: 6px; fill: var(--brand-blue); flex: none; }

  .address {
    position: absolute;
    left: 238px;
    top: 174px;
    margin: 0;
    font-style: normal;
    font-size: 12px;
    line-height: 16px;
    color: var(--ink);
  }

  .web-band {
    position: absolute;
    left: 0; bottom: 0;
    width: 442px; height: 40px;
    background: var(--brand-blue);
    color: var(--card-white);
    font-size: 14px;
    font-weight: 500;
    display: flex; align-items: center; justify-content: center;
  }
  .card--front .web-address {
    position: absolute;
    left: 0; width: 442px; top: 226px;
    margin: 0;
    text-align: center;
    color: var(--card-white);
    font-size: 14px;
    font-weight: 500;
  }
</style>
</head>
<body>
<main class="canvas">
  <section class="card card--back" aria-label="Card back with contact details">
    <p class="wordmark">VALMIRA</p>
    <p class="tagline">Integrative Holistic Medicine</p>

    <div class="holder">
      <h1 class="holder__name">TOBIAS WRENFELD</h1>
      <p class="holder__credentials">DOE,CPT,LMT</p>
    </div>

    <ul class="contact-list">
      <li><svg viewBox="0 0 10 10" aria-hidden="true"><path d="M3 0h4a1 1 0 0 1 1 1v8a1 1 0 0 1-1 1H3a1 1 0 0 1-1-1V1a1 1 0 0 1 1-1zm0 1.5v6h4v-6z"/></svg>512 555 0148</li>
      <li><svg viewBox="0 0 10 10" aria-hidden="true"><path d="M0 3.5C0 2 2 1 5 1s5 1 5 2.5V4.5H7.5V3.3Q5 2.7 2.5 3.3V4.5H0zM2 5.5h6l1 3.5H1z"/></svg>818 555 0192</li>
      <li><svg viewBox="0 0 10 10" aria-hidden="true"><path d="M0 2h10v6H0zm1 1v.3l4 2.4 4-2.4V3z"/></svg>info@ValmiraHealth.example</li>
      <li><svg viewBox="0 0 10 10" aria-hidden="true"><path d="M0 2h10v6H0zm1 1v.3l4 2.4 4-2.4V3z"/></svg>t.wrenfeld@ValmiraHealth.example</li>
    </ul>

    <address class="address">4100 East Marrow Drive<br>Austin, TX 78119</address>

    <div class="web-band">www.ValmiraHealth.example</div>
  </section>

  <section class="card card--front" aria-label="Card front with brand name">
    <p class="wordmark">VALMIRA</p>
    <p class="tagline">Integrative Holistic Medicine</p>
    <p class="web-address">www.ValmiraHealth.example</p>
  </section>
</main>
</body>
</html>
```